Powerpoint, Graphics for Sermon Series

I am starting a sermon series on the short letters if Scripture that are between Hebrews and Revelation. The sermon series will be called "Walking Unmarked Trails: Lasting Lessons from Quiet Hills."

Think about finding a packet of letters in an Attic. There is only the dialogue of the writer. We don't know exactly what the receivers were going through or even what their response to the letters were/are!

Target Market(s)

Local Church

Industry/Entity Type

Christian

Font styles to use
Serif
Sans Serif

Colors

Designer to choose colors to be used in the design.

Requirements
Must have
• Powerpoint Slide with Title -
• Background Slide -
• It would be great to have both JPG, PNG, and Photoshop/Indesign that can be used for powerpoint, both in 4x3 ration and wide... Need Title Slide with typography and background slide for text to go over the top of.
• Stick with the theme -- Walking Unmarked Trails
• I am including our church logo, but don't feel like you need to use it in anyway.
Nice to have
• Social Media Slides - Square Slide, Facebook Header
• Greyscale Version?

```html
<!DOCTYPE html>
<html lang="en">
<head>
<meta charset="utf-8">
<title>Sermon Slide – Content Layout</title>
<link rel="stylesheet" href="https://fonts.googleapis.com/css2?family=Cinzel:wght@700&family=Lato:wght@400;700&display=swap">
<style>
  :root {
    --bg: #ffffff;
    --header-bg: #f3f2f0;
    --title-brown: #6b3d1e;
    --accent-amber: #c4761c;
    --body-text: #4a4a4a;
    --footer-brown: #7a4d2b;
    --photo-dark: #2a1c12;
    --photo-mid: #6e5236;
    --photo-light: #c9a878;
  }
  * { margin: 0; padding: 0; box-sizing: border-box; }
  html, body {
    width: 1200px;
    height: 900px;
    overflow: hidden;
    background: var(--bg);
  }
  .slide {
    position: relative;
    width: 1200px;
    height: 900px;
    background: var(--bg);
  }
  .slide-header {
    position: absolute;
    top: 0; left: 0;
    width: 1200px;
    height: 140px;
    background: var(--header-bg);
  }
  .slide-title {
    position: absolute;
    left: 42px;
    top: 30px;
    font-family: "Cinzel", "Trajan Pro", serif;
    font-weight: 700;
    font-size: 51px;
    letter-spacing: 0.5px;
    color: var(--title-brown);
    line-height: 1.2;
  }
  .church-name {
    position: absolute;
    right: 22px;
    top: 52px;
    display: flex;
    align-items: center;
    gap: 10px;
    font-family: "Lato", sans-serif;
    font-weight: 700;
    font-size: 26px;
    color: var(--title-brown);
  }
  .church-name .mark {
    width: 14px;
    height: 14px;
    background: var(--title-brown);
  }
  .hero-photo {
    position: absolute;
    top: 140px; left: 0;
    width: 1200px;
    height: 493px;
    background:
      radial-gradient(ellipse 55% 60% at 42% 50%, var(--photo-light) 0%, rgba(180,145,100,0.85) 45%, rgba(110,82,54,0) 80%),
      linear-gradient(160deg, var(--photo-mid) 0%, var(--photo-dark) 100%);
  }
  .content {
    position: absolute;
    left: 37px;
    top: 660px;
    width: 1130px;
  }
  .subtext-title {
    font-family: "Lato", sans-serif;
    font-weight: 700;
    font-size: 33px;
    color: var(--accent-amber);
    line-height: 1.2;
    margin-bottom: 6px;
  }
  .body-copy {
    font-family: "Lato", sans-serif;
    font-weight: 400;
    font-size: 21.5px;
    line-height: 39px;
    color: var(--body-text);
  }
  .slide-footer {
    position: absolute;
    left: 0; bottom: 0;
    width: 1200px;
    height: 27px;
    background: var(--footer-brown);
  }
</style>
</head>
<body>
  <main class="slide">
    <header class="slide-header">
      <h1 class="slide-title">SLIDE TITLE HERE</h1>
      <div class="church-name"><span class="mark"></span>Hollow Creek Chapel</div>
    </header>

    <div class="hero-photo" role="img" aria-label="Photograph of aged handwritten letters on parchment lying on a dark wooden desk beside pencils"></div>

    <section class="content">
      <h2 class="subtext-title">Subtext title here</h2>
      <p class="body-copy">Lorem Ipsum is simply dummy text of the printing and typesetting industry. Lorem Ipsum has been the industry's standard dummy text ever since the 1500s, when an unknown printer took a galley of type and scrambled it to make a type specimen book. It has survived not only five centuries, but also the leap into electronic typesetting, remaining essentially unchanged. It was popularised in the 1960s with the release .</p>
    </section>

    <footer class="slide-footer"></footer>
  </main>
</body>
</html>
```